Ward Compass Business Card Design*

We need a business card design for our company Ward Compass. Our company is specialized in providing online consulting services regarding medical institutions, hospitals and doctors. We work with patients worldwide looking to choose between healthcare providers. We have a website you may use as a reference, where we list doctors and clinics worldwide. So we target Medical providers as well as patients worldwide.
Target Market(s)
Medical Providers and patients around the world
Industry/Entity Type
Medical
Contact Information for Business Card
Salwa Kettani
CEO
+90 612 348 2175
info@wardcompass.example
www.wardcompass.example
14 Annakhil 7 H.R.B. Rabat, Morocco
Requirements
Must have
- Company logo/name on one full side, personal info and smaller logo and company name on the other side.
Nice to have
- Smart and elegant design

```html
<!DOCTYPE html>
<html lang="en">
<head>
<meta charset="utf-8">
<title>Ward Compass — Business Card</title>
<link rel="stylesheet" href="https://fonts.googleapis.com/css2?family=Poppins:wght@400;500&display=swap">
<style>
  :root {
    --backdrop: #e4e4e4;
    --paper: #ffffff;
    --navy: #1b4470;
    --navy-top: #1f4d7d;
    --navy-bottom: #133868;
    --grey-text: #6f6f6f;
    --body-text: #4a4a4a;
    --white: #ffffff;
  }
  * { box-sizing: border-box; margin: 0; padding: 0; }
  html, body {
    width: 1200px;
    height: 1200px;
    overflow: hidden;
    background: var(--backdrop);
    font-family: "Poppins", sans-serif;
  }
  .card {
    position: absolute;
    left: 257px;
    width: 686px;
    height: 392px;
  }
  .card-front {
    top: 165px;
    background: var(--paper);
  }
  .card-back {
    top: 653px;
    background: linear-gradient(180deg, var(--navy-top), var(--navy-bottom));
    display: flex;
    align-items: center;
    justify-content: center;
  }
  .front-brand {
    position: absolute;
    top: 40px;
    right: 38px;
    display: flex;
    align-items: center;
    gap: 12px;
  }
  .brand-dot {
    width: 40px;
    height: 40px;
    border-radius: 50%;
    background: var(--navy);
  }
  .front-brand .brand-name {
    color: var(--navy);
    font-weight: 500;
    font-size: 20px;
    letter-spacing: 0.5px;
  }
  .person {
    position: absolute;
    left: 35px;
    top: 222px;
  }
  .person-name {
    color: var(--navy);
    font-weight: 500;
    font-size: 25px;
    line-height: 1.1;
    text-transform: uppercase;
  }
  .person-role {
    color: var(--grey-text);
    font-size: 14px;
    margin-top: 2px;
    margin-left: 1px;
  }
  .contact {
    margin-top: 14px;
    margin-left: 2px;
    color: var(--body-text);
    font-size: 15px;
    line-height: 20px;
  }
  .contact .address { margin-top: 8px; }
  .back-brand {
    display: flex;
    align-items: center;
    gap: 18px;
  }
  .back-brand .brand-dot {
    width: 64px;
    height: 64px;
    background: var(--white);
  }
  .back-brand .brand-name {
    color: var(--white);
    font-weight: 500;
    font-size: 30px;
    letter-spacing: 1px;
    text-transform: uppercase;
  }
</style>
</head>
<body>
  <section class="card card-front">
    <div class="front-brand">
      <span class="brand-dot"></span>
      <span class="brand-name">Ward Compass</span>
    </div>
    <div class="person">
      <h1 class="person-name">Salwa Kettani</h1>
      <p class="person-role">CEO</p>
      <div class="contact">
        <p>P: +90 612 348 2175</p>
        <p>E: info@wardcompass.example W: wardcompass.example</p>
        <p class="address">14 Annakhil 7, H.R.B. Rabat, Morocco</p>
      </div>
    </div>
  </section>

  <section class="card card-back">
    <div class="back-brand">
      <span class="brand-dot"></span>
      <span class="brand-name">Ward Compass</span>
    </div>
  </section>
</body>
</html>
```